Indonesian B2B Company (Bawo Ingredients) - Stationery Design

Bawo Ingredients needs a corporate, bold and professional-looking stationery design.

Bawo Ingredients is a new Indonesian company manufacturing, marketing and distributing various ingredients / raw materials such as flavours, fragrance, colours, sweeteners, preservatives for the food & beverage, pharmaceutical, personal care and other household goods industries.

It is a business to business (B2B) company as we supply various natural and synthetic raw materials to various consumer goods manufacturers. We therefore need a logo/identity with corporate and industrial style.

Bawo Ingredients is a startup company which belongs to a larger Tunas Mekar group of companies (http://tunasmekar.examplebiz.net/about) that focuses in the mining, petroleum and energy businesses. Bawo Ingredients would like to focus in providing good quality, safe, reliable and affordable ingredients for the industries. Our tagline is "Ingredients for Your Success"
Updates

We have updated some information including our requirements and contact details to be shown in the stationery. Please check the project brief.

Regards,

Bawo Ingredients

Target Market(s)

Manufacturers of food & beverages, personal care, pharmaceutical and other FMCG factories.

Industry/Entity Type

Business

Requirements
Must have
• Smart, professional and corporate touches in the stationery designs. We require designs for:
1. Letterhead
2. Envelope (with and without window)
3. Name card
4. Powerpoint presentation template
5. CD label
6. Small memo / with compliments card

Contact details:

Company name:
PT Bawo Ingredients

Address:
Ruko Puri Lestari Selatan, Blok F07 no: 11-12
Sunter Jaya Utara, 14350
Indonesia

Tel:+62 21 638 2097
Fax:+62 21 638 2096
Email: info@bawo-ingredients.co.id
Website: www.bawo-ingredients.co.id

```html
<!DOCTYPE html>
<html lang="en">
<head>
<meta charset="utf-8">
<title>Bawo Ingredients – Compliment Card</title>
<link rel="stylesheet" href="https://fonts.googleapis.com/css2?family=PT+Sans:wght@400;700&family=Open+Sans:wght@400;600&family=Marcellus&display=swap">
<style>
  :root {
    --stage: #2c2c2c;
    --label: #ffffff;
    --brand-blue: #2a8bd8;
    --brand-blue-deep: #1b6fbd;
    --brand-blue-dark: #1766b3;
    --brand-blue-soft: #3b97df;
    --band-light: #84c8f8;
    --heading-blue: #1a73c2;
    --brand-red: #e8504a;
    --name-red: #d9322f;
    --ink: #111111;
    --muted: #9a9a9a;
    --tagline-light: #c9d9ea;
    --paper: #ffffff;
  }
  * { box-sizing: border-box; margin: 0; padding: 0; }
  html, body {
    width: 1039px; height: 1200px; overflow: hidden;
    background: var(--stage);
    font-family: "Open Sans", Arial, sans-serif;
  }
  .sheet { position: relative; width: 1039px; height: 1200px; }

  .sheet-label {
    position: absolute; left: 0; width: 100%;
    text-align: center; color: var(--label);
    font-family: "Marcellus", Georgia, serif;
    font-size: 28px; font-weight: 400;
  }
  .sheet-label--front { top: 50px; }
  .sheet-label--back { top: 1124px; }

  /* Front */
  .card-front {
    position: absolute; left: 35px; top: 133px;
    width: 946px; height: 407px;
    background: var(--brand-blue); overflow: hidden;
  }
  .card-front__decor {
    position: absolute; left: 395px; top: 0; width: 551px; height: 368px;
    background:
      linear-gradient(160deg, var(--brand-blue-dark) 0%, var(--brand-blue-deep) 18%, transparent 32%),
      linear-gradient(45deg, var(--band-light) 0%, var(--brand-blue-soft) 30%, var(--brand-blue-deep) 62%, var(--brand-blue-dark) 100%);
  }
  .card-front__band-top {
    position: absolute; left: 0; top: 0; width: 372px; height: 37px;
    background: var(--band-light);
  }
  .card-front__band-bottom {
    position: absolute; left: 499px; top: 368px; width: 447px; height: 39px;
    background: var(--band-light);
  }
  .card-front__mark {
    position: absolute; left: 125px; top: 165px; width: 90px; height: 90px;
    background: var(--brand-red);
  }
  .card-front__identity { position: absolute; left: 67px; top: 295px; }
  .card-front__name {
    font-family: "PT Sans", Arial, sans-serif;
    color: var(--paper); font-size: 36px; font-weight: 400; line-height: 1;
  }
  .card-front__tagline {
    font-family: "PT Sans", Arial, sans-serif;
    color: var(--tagline-light); font-size: 18px; margin-top: 6px; margin-left: 12px;
  }

  /* Back */
  .card-back {
    position: absolute; left: 39px; top: 675px;
    width: 945px; height: 405px;
    background: var(--paper); overflow: hidden;
  }
  .card-back__decor {
    position: absolute; left: 581px; top: 0; width: 364px; height: 405px;
    background: linear-gradient(135deg, rgba(27,111,189,.08) 0%, rgba(232,80,74,.10) 45%, rgba(245,180,60,.10) 100%);
  }
  .message { position: absolute; left: 41px; top: 40px; width: 600px; }
  .message__heading {
    color: var(--heading-blue); font-size: 18px; font-weight: 600; margin-bottom: 9px;
  }
  .message__body p {
    color: var(--ink); font-size: 14px; line-height: 19.5px; margin-bottom: 18px;
    letter-spacing: -0.1px;
  }
  .card-back__bar {
    position: absolute; left: 41px; top: 368px; width: 547px; height: 37px;
    background: var(--brand-blue-deep);
  }
  .card-back__bar-accent {
    position: absolute; left: 588px; top: 368px; width: 48px; height: 37px;
    background: var(--brand-red);
  }
  .contact__mark {
    position: absolute; left: 744px; top: 24px; width: 70px; height: 70px;
    background: var(--brand-red);
  }
  .contact { position: absolute; left: 680px; top: 107px; width: 255px; }
  .contact__name {
    font-family: "PT Sans", Arial, sans-serif;
    color: var(--name-red); font-size: 22px; line-height: 1;
  }
  .contact__tagline {
    font-family: "PT Sans", Arial, sans-serif;
    color: var(--muted); font-size: 12px; margin: 3px 0 0 10px;
  }
  .contact__label { color: var(--heading-blue); font-size: 13px; margin-top: 16px; }
  .contact__value { color: var(--ink); font-size: 13px; line-height: 18.5px; }
</style>
</head>
<body>
<main class="sheet">
  <h2 class="sheet-label sheet-label--front">Compliment Card Front</h2>

  <section class="card-front">
    <div class="card-front__decor" role="img" aria-label="Large brand mark decoration in layered blues"></div>
    <div class="card-front__band-top"></div>
    <div class="card-front__band-bottom"></div>
    <div class="card-front__mark"></div>
    <div class="card-front__identity">
      <div class="card-front__name">Bawo Ingredients</div>
      <div class="card-front__tagline">Ingredients for Your Success</div>
    </div>
  </section>

  <section class="card-back">
    <div class="card-back__decor" role="img" aria-label="Faint brand mark decoration"></div>
    <div class="message">
      <h3 class="message__heading">Compliments:</h3>
      <div class="message__body">
        <p>Lorem Ipsum is simply dummy text of the printing and typesetting industry. Lorem Ipsum has been the industry's standard dummy text ever since the 1500s, when an unknown printer took a galley of type and scrambled.</p>
        <p>Lorem Ipsum is simply dummy text of the printing and typesetting industry. Lorem Ipsum has been the industry's standard dummy text ever since the 1500s, when an unknown printer took a galley of type and scrambled.</p>
        <p>Lorem Ipsum is simply dummy text of the printing and typesetting industry. Lorem Ipsum has been the industry's standard dummy text ever since the 1500s, when an unknown printer took a galley of type and scrambled. Lorem Ipsum is simply dummy text of the printing and typesetting industry. Lorem Ipsum has been the industry's standard dummy text ever since the 1500s, when an unknown printer took...</p>
      </div>
    </div>
    <div class="card-back__bar"></div>
    <div class="card-back__bar-accent"></div>

    <div class="contact__mark"></div>
    <div class="contact">
      <div class="contact__name">Bawo Ingredients</div>
      <div class="contact__tagline">Ingredients for Your Success</div>
      <div class="contact__label">Address:</div>
      <div class="contact__value">Ruko Puri Lestari Selatan,<br>Blok F07 no: 11-12 Sunter<br>Jaya Utara, 14350<br>Indonesia.</div>
      <div class="contact__label">Web/Email:</div>
      <div class="contact__value">info@bawo-ingredients.co.id<br>www.bawo-ingredients.co.id</div>
      <div class="contact__label">Phones:</div>
      <div class="contact__value">+62 21 638 2096, +62 21 638 2097</div>
    </div>
  </section>

  <h2 class="sheet-label sheet-label--back">Compliment Card Back</h2>
</main>
</body>
</html>
```